To design a brand identity that is simple and creative with 'Corvane' as the brand name, I like modern simple fonts like helvetica neue, I want to print both sides of the card, I am open to dark front and white back, but the design needs to transfer well to letter heads and email signatures, I am looking for sophisticated and elegant, but open minded about clever and off the wall, I do not do 'boring' Corvane Ventures is the mother company for a small group, specialising in Management & consulting, Software development and construction, we have a high level of integrity, we are transparent and accountable for what we do. my images are provided as a guide only, Im not expecting them to be just copied, Im looking for a creator and passionate thinker, who will put life into their work.

Target Market(s)

usually business minded people who are looking for something different in me, such as leadership, confidence and focus with thinking that is per haps a little outside the box..

Industry/Entity Type

Construction

Requirements
Must have
• clean, minmalistic
Nice to have
• custom logo
Should not have
• boring, traditional

```html
<!DOCTYPE html>
<html lang="en">
<head>
<meta charset="utf-8">
<title>Corvane Business Card</title>
<link href="https://fonts.googleapis.com/css2?family=Inter:wght@300;400&display=swap" rel="stylesheet">
<style>
  :root {
    --backdrop: #37332f;
    --plum: #8a2c6b;
    --coral: #ea3e36;
    --white: #ffffff;
    --faint: rgba(255, 255, 255, 0.18);
    --charcoal-glow: #575351;
    --charcoal: #2b2b2b;
    --mark: #f1b443;
    --dot: #d23a3a;
    --soft-text: #e9e6e4;
  }
  * { margin: 0; padding: 0; box-sizing: border-box; }
  html, body { width: 1000px; height: 1200px; overflow: hidden; }
  body {
    position: relative;
    background: var(--backdrop);
    font-family: "Inter", "Helvetica Neue", Arial, sans-serif;
    font-weight: 300;
    color: var(--white);
  }
  .card {
    position: absolute;
    width: 740px;
    height: 458px;
    overflow: hidden;
  }
  /* Front */
  .card-front {
    left: 136px; top: 74px;
    background: linear-gradient(90deg, var(--plum) 0%, #b4334f 50%, var(--coral) 85%);
  }
  .brand-lockup {
    position: absolute;
    left: 46px; top: 212px;
    display: flex; align-items: center; gap: 20px;
  }
  .brand-dot {
    width: 46px; height: 46px; border-radius: 50%;
    background: var(--mark);
  }
  .brand-name {
    font-size: 46px; line-height: 1; letter-spacing: -0.5px;
    font-weight: 300;
  }
  .brand-tagline {
    position: absolute;
    left: 134px; top: 266px;
    font-size: 12px; letter-spacing: 0.3px;
    color: var(--soft-text);
  }
  .vertical {
    position: absolute;
    writing-mode: vertical-rl;
    transform: rotate(180deg);
    white-space: nowrap;
  }
  .front-watermark {
    left: 330px; top: 108px;
    font-size: 68px; line-height: 1;
    color: var(--faint);
    font-weight: 300;
  }
  .front-services {
    left: 361px; top: 56px; height: 346px;
    font-size: 15px; letter-spacing: 1.3px;
    text-align: center;
  }
  .contact {
    position: absolute;
    left: 454px; top: 138px;
  }
  .contact-name { font-size: 26px; font-weight: 400; line-height: 1.2; }
  .contact-role { font-size: 16px; font-weight: 400; margin-bottom: 6px; }
  .contact-line { font-size: 18.5px; line-height: 28px; letter-spacing: 0.6px; color: var(--soft-text); }
  .contact-gap { margin-top: 13px; }
  /* Back */
  .card-back {
    left: 117px; top: 651px;
    background: radial-gradient(ellipse 60% 65% at 50% 45%, var(--charcoal-glow) 0%, #3c3a39 55%, var(--charcoal) 100%);
  }
  .back-lockup {
    position: absolute;
    left: 0; right: 0; top: 170px;
    display: flex; justify-content: center; align-items: center; gap: 26px;
  }
  .back-dot {
    width: 84px; height: 84px; border-radius: 50%;
    background: var(--mark);
  }
  .back-name { font-size: 96px; line-height: 1; letter-spacing: -1px; font-weight: 300; }
  .back-services {
    position: absolute;
    left: 0; right: 0; top: 296px;
    text-align: center;
    font-size: 16px; letter-spacing: 1.5px;
    color: var(--soft-text);
  }
  .sep {
    display: inline-block; width: 5px; height: 5px; border-radius: 50%;
    background: var(--dot); margin: 0 9px; vertical-align: middle;
  }
</style>
</head>
<body>
  <section class="card card-front" aria-label="Business card front">
    <div class="brand-lockup">
      <span class="brand-dot" aria-hidden="true"></span>
      <span class="brand-name">corvane</span>
    </div>
    <p class="brand-tagline">... shaping what comes next</p>
    <div class="vertical front-watermark" aria-hidden="true">corvane</div>
    <p class="vertical front-services">management • software • construction</p>
    <div class="contact">
      <p class="contact-name">Mara Linden</p>
      <p class="contact-role">client ambassador</p>
      <p class="contact-line">c. +61 0400 555 012</p>
      <p class="contact-line">e. info@corvane.com.au</p>
      <p class="contact-line contact-gap">a. po box 512 ridgeford 6100</p>
      <p class="contact-line">w. www.corvane.com.au</p>
    </div>
  </section>

  <section class="card card-back" aria-label="Business card back">
    <div class="back-lockup">
      <span class="back-dot" aria-hidden="true"></span>
      <span class="back-name">corvane.</span>
    </div>
    <p class="back-services">management<span class="sep"></span>software<span class="sep"></span>construction</p>
  </section>
</body>
</html>
```